Re-style home page - eye-catching and unique design for social commerce website

We need a new concept design for BrinoKet's home page.
We don't want to make huge changes but creating a more professional and eye-catching style.

We need to look very serious like a professional services company and in the same time to look like a social network for e-commerce.

Our logo is very captive and you can use to creating something of harmonious.

This is a re-style and I'm excepted to see unique and fresh design like Glimmora.

Target Market(s)

e-commerce and social

Industry/Entity Type

Social

Number of Pages Required

1 page

Font styles to use
Serif
Sans Serif

Requirements
Must have
• An eye-catching result.
• Search bar with logo and Login How it works and business
• The slogan with login and signup.
• Footer links.
Nice to have
• I would like to open the home page and see only two clear ways:
• -Consumer
• --Search
• --The slogan
• --Login and Signup
• --How it works
• -Business
• --Go to Business area
• Background: City, Shopping.
Should not have
• Scrollbar style!

```html
<!DOCTYPE html>
<html lang="en">
<head>
<meta charset="utf-8">
<title>BrinoKet – Shop directly from your profile</title>
<link rel="stylesheet" href="https://fonts.googleapis.com/css2?family=Montserrat:wght@400;500;600;700&family=Open+Sans:wght@300;400&display=swap">
<style>
  :root {
    --night: #1c1f45;
    --night-deep: #15173a;
    --header-bg: rgba(28, 30, 68, 0.72);
    --field-bg: rgba(255, 255, 255, 0.14);
    --white: #ffffff;
    --ink: #3a3a48;
    --muted: #9a9aa6;
    --signup: #d1312f;
    --business: #7cb82f;
    --hero-navy: rgba(35, 43, 85, 0.92);
    --hero-light: rgba(236, 236, 240, 0.85);
  }
  * { box-sizing: border-box; margin: 0; padding: 0; }
  html, body { width: 1200px; height: 675px; overflow: hidden; background: var(--night-deep); }
  .page {
    position: relative;
    width: 1200px;
    height: 675px;
    overflow: hidden;
    font-family: "Montserrat", Arial, sans-serif;
    color: var(--white);
  }
  a { color: inherit; text-decoration: none; }
  .city-backdrop {
    position: absolute; inset: 0;
    background:
      radial-gradient(ellipse at 70% 35%, rgba(150, 135, 175, 0.55), transparent 55%),
      radial-gradient(ellipse at 18% 40%, rgba(120, 95, 110, 0.5), transparent 50%),
      linear-gradient(180deg, #4b4475 0%, #3d3766 45%, #2b2a58 75%, #1f2049 100%);
  }

  /* header */
  .site-header {
    position: absolute; left: 0; top: 0; width: 1200px; height: 59px;
    background: var(--header-bg);
  }
  .brand {
    position: absolute; left: 26px; top: 12px;
    display: flex; align-items: center; gap: 9px;
    font-weight: 700; font-size: 28px; letter-spacing: -0.5px; line-height: 34px;
  }
  .brand-dot { width: 14px; height: 14px; border-radius: 50%; background: var(--white); }
  .search-field {
    position: absolute; left: 411px; top: 11px; width: 400px; height: 35px;
    background: var(--field-bg); border-radius: 3px;
    font-family: "Open Sans", Arial, sans-serif; font-size: 13px;
    color: rgba(255, 255, 255, 0.55); line-height: 35px; padding-left: 17px;
  }
  .search-icon { position: absolute; left: 829px; top: 19px; }
  .login-link { position: absolute; left: 871px; top: 20px; font-size: 13px; font-weight: 500; }

  /* hero illustration area */
  .hero-illustration {
    position: absolute; left: 421px; top: 100px; width: 354px; height: 201px;
    border-radius: 6px;
    background:
      radial-gradient(ellipse at 50% 62%, var(--hero-light) 0%, rgba(236, 236, 240, 0.35) 32%, transparent 55%),
      radial-gradient(ellipse at 50% 55%, var(--hero-navy) 0%, rgba(35, 43, 85, 0.6) 55%, rgba(35, 43, 85, 0) 100%);
  }

  /* hero copy */
  .slogan {
    position: absolute; left: 0; top: 332px; width: 1200px; text-align: center;
    font-family: "Open Sans", Arial, sans-serif; font-weight: 300; font-size: 35px; line-height: 46px;
  }
  .feed-setup { position: absolute; top: 395px; left: 0; width: 1200px; height: 34px; }
  .feed-label { position: absolute; left: 330px; top: 10px; font-size: 11px; font-weight: 600; }
  .select {
    position: absolute; top: 0; width: 176px; height: 34px; background: var(--white);
    border-radius: 2px; color: var(--ink);
    font-family: "Open Sans", Arial, sans-serif; font-size: 12.5px; line-height: 34px;
  }
  .select-interest { left: 433px; padding-left: 13px; }
  .select-city { left: 618px; padding-left: 28px; }
  .select .chevron { position: absolute; right: 12px; top: 13px; }
  .select .pin { position: absolute; left: 11px; top: 10px; }
  .signup-button {
    position: absolute; left: 807px; top: 0; width: 84px; height: 34px;
    background: var(--signup); border-radius: 2px; text-align: center;
    font-size: 13px; font-weight: 500; line-height: 34px;
  }
  .business-button {
    position: absolute; left: 511px; top: 459px; width: 179px; height: 35px;
    background: var(--business); border-radius: 2px;
    display: flex; align-items: center; justify-content: center; gap: 7px;
    font-size: 12.5px; font-weight: 500;
  }
  .how-it-works {
    position: absolute; left: 0; top: 505px; width: 1200px; text-align: center;
    font-size: 11.5px; font-weight: 500;
  }

  /* footer */
  .site-footer { position: absolute; left: 0; top: 575px; width: 1200px; text-align: center; }
  .footer-links { display: flex; justify-content: center; gap: 28px; list-style: none; font-size: 10.5px; font-weight: 500; margin-left: 8px; }
  .copyright { margin-top: 13px; font-size: 9px; font-weight: 500; }
</style>
</head>
<body>
<div class="page">
  <div class="city-backdrop" role="img" aria-label="Blurred photo of a busy city shopping street with crowds of shoppers, tinted deep purple"></div>

  <header class="site-header">
    <div class="brand"><span>BrinoKet</span><span class="brand-dot"></span></div>
    <div class="search-field">Search keyword</div>
    <svg class="search-icon" width="20" height="20" viewBox="0 0 20 20" aria-hidden="true">
      <circle cx="8.5" cy="8.5" r="6.5" fill="none" stroke="#fff" stroke-width="2.4"/>
      <line x1="13.3" y1="13.3" x2="18" y2="18" stroke="#fff" stroke-width="2.6" stroke-linecap="round"/>
    </svg>
    <a class="login-link">Login</a>
  </header>

  <div class="hero-illustration" role="img" aria-label="Illustration of a browser window showing a profile feed, connected by dotted lines to four circular shopper profile photos"></div>

  <h1 class="slogan">Shop directly from your profile</h1>

  <div class="feed-setup">
    <span class="feed-label">Setup your feed</span>
    <div class="select select-interest">Active life
      <svg class="chevron" width="12" height="8" viewBox="0 0 12 8" aria-hidden="true"><path d="M1 1l5 5 5-5" fill="none" stroke="#9a9aa6" stroke-width="1.4"/></svg>
    </div>
    <div class="select select-city">
      <svg class="pin" width="10" height="14" viewBox="0 0 10 14" aria-hidden="true"><path d="M5 0a5 5 0 0 0-5 5c0 3.7 5 9 5 9s5-5.3 5-9a5 5 0 0 0-5-5zm0 7a2 2 0 1 1 0-4 2 2 0 0 1 0 4z" fill="#9a9aa6"/></svg>
      London
      <svg class="chevron" width="12" height="8" viewBox="0 0 12 8" aria-hidden="true"><path d="M1 1l5 5 5-5" fill="none" stroke="#9a9aa6" stroke-width="1.4"/></svg>
    </div>
    <a class="signup-button">Sign Up</a>
  </div>

  <a class="business-button">Go to Business Area
    <svg width="18" height="8" viewBox="0 0 18 8" aria-hidden="true"><path d="M0 4h16M13 1l3 3-3 3" fill="none" stroke="#fff" stroke-width="1.1"/></svg>
  </a>
  <a class="how-it-works">How it works</a>

  <footer class="site-footer">
    <ul class="footer-links">
      <li>About Us</li><li>Blog</li><li>Business</li><li>Jobs</li><li>Privacy</li><li>FAQ</li><li>Contacts</li>
    </ul>
    <p class="copyright">© 2015 BrinoKet. All right reserved.</p>
  </footer>
</div>
</body>
</html>
```